BildeVOLD buisnesscard

Hey :) I need a modern buisnesscard for my company BildeVOLD
It most have:
Dagligleder og Fotograf: Henrik Audun Strandvik

Mob: +4791264085
Epost: post@bildevold.example
Adresse: Kvernbakken9, 6040 Fjordvik

Facbook and instagram logo with text BildeVOLD

BildeVOLD logo

It Company

```html
<!DOCTYPE html>
<html lang="no">
<head>
<meta charset="utf-8">
<title>BildeVOLD – Business Card</title>
<link rel="stylesheet" href="https://fonts.googleapis.com/css2?family=Khand:wght@600&family=Roboto:wght@400;700&display=swap">
<style>
  :root {
    --bg: #e4e4e4;
    --front-top: #bcbdbf;
    --front-bottom: #8d8f92;
    --paper: #fbfbfb;
    --strip: #97989a;
    --strip-edge: #6e6f71;
    --ink: #8b8c8e;
    --ink-soft: #a5a6a8;
    --white: #ffffff;
  }
  * { margin: 0; padding: 0; box-sizing: border-box; }
  html, body { width: 1200px; height: 576px; overflow: hidden; background: var(--bg); }
  .canvas { position: relative; width: 1200px; height: 576px; font-family: "Roboto", sans-serif; }

  .card { position: absolute; border-radius: 9px; overflow: hidden; box-shadow: 0 2px 5px rgba(0,0,0,.22); }

  /* Front */
  .card--front {
    left: 82px; top: 138px; width: 486px; height: 296px;
    background: linear-gradient(180deg, var(--front-top) 0%, #a6a7a9 45%, var(--front-bottom) 100%);
  }
  .front-brand {
    position: absolute; left: 0; right: 0; top: 94px;
    display: flex; flex-direction: column; align-items: center; gap: 8px;
  }
  .front-brand__mark { width: 74px; height: 72px; background: var(--white); }
  .front-brand__name { font-weight: 700; font-size: 37px; letter-spacing: .3px; color: var(--white); line-height: 1; }

  /* Back */
  .card--back {
    left: 602px; top: 138px; width: 481px; height: 292px;
    background: var(--paper);
  }
  .back-strip {
    position: absolute; left: 0; top: 0; bottom: 0; width: 43px;
    background: var(--strip); border-right: 4px solid var(--strip-edge);
  }
  .back-brand {
    position: absolute; right: 30px; top: 28px;
    display: flex; align-items: center; gap: 14px;
  }
  .back-brand__mark { width: 46px; height: 46px; background: var(--ink); }
  .back-brand__rule { width: 1px; height: 50px; background: var(--ink-soft); }
  .back-brand__name { font-weight: 700; font-size: 27px; color: var(--ink); line-height: 1; }

  .person { position: absolute; left: 64px; top: 160px; }
  .person__name { font-family: "Khand", sans-serif; font-weight: 600; font-size: 21px; color: var(--ink); line-height: 1.1; }
  .person__title { font-size: 12px; color: var(--ink); margin-top: 3px; }

  .contacts { position: absolute; top: 213px; list-style: none; }
  .contacts--main { left: 64px; }
  .contacts--web { left: 308px; }
  .contacts li {
    display: flex; align-items: center; gap: 10px;
    font-size: 13.5px; color: var(--ink); height: 17.5px;
  }
  .contacts svg { width: 11px; height: 11px; fill: var(--ink); flex: none; }
  .contacts .dot { width: 10px; height: 10px; background: var(--ink); border-radius: 2px; flex: none; margin-right: 1px; }
</style>
</head>
<body>
<main class="canvas">
  <section class="card card--front" aria-label="Card front">
    <div class="front-brand">
      <div class="front-brand__mark"></div>
      <div class="front-brand__name">BildeVOLD</div>
    </div>
  </section>

  <section class="card card--back" aria-label="Card back">
    <div class="back-strip"></div>
    <div class="back-brand">
      <div class="back-brand__mark"></div>
      <div class="back-brand__rule"></div>
      <div class="back-brand__name">BildeVOLD</div>
    </div>

    <div class="person">
      <div class="person__name">Henrik Audun Strandvik</div>
      <div class="person__title">Managing Director &amp; Photographer</div>
    </div>

    <ul class="contacts contacts--main">
      <li>
        <svg viewBox="0 0 12 12"><path d="M3 0h6a1 1 0 0 1 1 1v10a1 1 0 0 1-1 1H3a1 1 0 0 1-1-1V1a1 1 0 0 1 1-1zm0 1.5v8h6v-8zM5 10.2h2v.8H5z"/></svg>
        +4791264085
      </li>
      <li>
        <svg viewBox="0 0 12 12"><path d="M0 2h12v8H0zm1 1v.4l5 3.2 5-3.2V3zm0 1.6V9h10V4.6L6 7.8z"/></svg>
        post@bildevold.example
      </li>
      <li>
        <svg viewBox="0 0 12 12"><path d="M6 0a4 4 0 0 1 4 4c0 3-4 8-4 8S2 7 2 4a4 4 0 0 1 4-4zm0 2.4A1.6 1.6 0 1 0 6 5.6 1.6 1.6 0 0 0 6 2.4z"/></svg>
        Kvernbakken9, 6040 Fjordvik
      </li>
    </ul>

    <ul class="contacts contacts--web">
      <li><span class="dot"></span>/BildeVOLD</li>
      <li><span class="dot"></span>/BildeVOLD</li>
      <li>
        <svg viewBox="0 0 12 12"><path d="M6 0a6 6 0 1 1 0 12A6 6 0 0 1 6 0zm-.6 1.3A4.8 4.8 0 0 0 1.3 5.4h2.2c.1-1.6.8-3 1.9-4.1zm1.2 0c1.1 1.1 1.8 2.5 1.9 4.1h2.2a4.8 4.8 0 0 0-4.1-4.1zM4.7 5.4h2.6C7.2 4 6.7 2.8 6 2c-.7.8-1.2 2-1.3 3.4zm-3.4 1.2a4.8 4.8 0 0 0 4.1 4.1c-1.1-1.1-1.8-2.5-1.9-4.1zm3.4 0c.1 1.4.6 2.6 1.3 3.4.7-.8 1.2-2 1.3-3.4zm3.8 0c-.1 1.6-.8 3-1.9 4.1a4.8 4.8 0 0 0 4.1-4.1z"/></svg>
        www.bildevold.example
      </li>
    </ul>
  </section>
</main>
</body>
</html>
```